The design should look similar to the uploaded example to accommodate the information needed for a business card template. I would like to see the colors orange and charcoal grey incorporated along with the logo.The following should be on the back of the card SPECIALIZING IN NEW AND USED TIRES & WHEELS FOR:- Loaders- Skid Steers- Telehandlers- Boom Lifts- Forklifs and moreELIMINATING DOWNTIMEWheel Exchange Program for New & Used Foam Filled and Solid Rubber TiresSPECIALTY SERVICES- Foam Filling Tires- Largest Tire Press in SE- ONSITE Forklift Tire Press- Boom Truck Services - Rubber Tracks

Target Market(s)

New and Existing Customers

Industry/Entity Type

Business

Contact Information for Business Card

NAMEHEAVY DUTY TIRE, LLC8470 Belvedere RoadWest Palm Beach, FL 33411P: 844-HD-TIRESF: 561-431-6469C:E: W: WWW.GRANITERIMSUPPLY-EXAMPLE.COM

Font styles to use
Sans Serif

Colors
f37122
333333

Requirements
Must have
• The logo and the information indicated for the backside of the card
Nice to have
• Keep the orange and charcoal grey colors

```html
<!DOCTYPE html>
<html lang="en">
<head>
<meta charset="utf-8">
<title>Granite Rim Supply – Business Card</title>
<link rel="stylesheet" href="https://fonts.googleapis.com/css2?family=Open+Sans:wght@400;600;700&family=Oswald:wght@700&display=swap">
<style>
  :root{
    --orange:#f37122;
    --charcoal:#333333;
    --band:#4a4a4a;
    --page:#3a3532;
    --white:#ffffff;
    --rule:#555555;
    --muted:#9a9a9a;
    --badge:#d6d6d6;
  }
  *{box-sizing:border-box;margin:0;padding:0}
  html,body{width:1200px;height:799px;overflow:hidden;background:var(--page)}
  .stage{position:relative;width:1200px;height:799px}
  .card{position:absolute;top:250px;width:520px;height:300px;background:var(--white);overflow:hidden;
    font-family:"Open Sans",Arial,sans-serif;color:var(--charcoal);box-shadow:0 10px 24px rgba(0,0,0,.45)}
  .card--back{left:45px}
  .card--front{left:635px}

  /* brand mark */
  .brand{position:absolute;display:flex;align-items:center;gap:8px}
  .brand__dot{width:50px;height:50px;border-radius:50%;background:var(--orange);flex:none}
  .brand__name{font-weight:700;font-size:13px;line-height:1.15;color:var(--charcoal);width:66px}

  /* back */
  .card--back .brand{left:20px;top:14px}
  .services__title{position:absolute;left:180px;top:36px;font-size:22px;font-weight:400;letter-spacing:.5px;color:var(--charcoal);white-space:nowrap}
  .services__rule{position:absolute;left:150px;top:70px;width:352px;height:2px;background:var(--rule)}

  .range{position:absolute;left:24px;top:86px;width:240px}
  .range__title{font-size:10px;font-weight:700;line-height:13px;color:var(--orange);letter-spacing:.2px}
  .range__list{list-style:none;margin-top:5px;font-size:12.5px;line-height:17px}
  .downtime{position:absolute;left:24px;top:222px;width:245px}
  .downtime__title{font-size:13px;font-weight:700;color:var(--orange);letter-spacing:.5px;line-height:17px}
  .downtime__text{font-size:10.5px;line-height:14px;color:var(--charcoal);margin-top:2px}

  .services__list{position:absolute;left:282px;top:90px;list-style:none;font-size:14px;line-height:23px}
  .bullets li{position:relative;padding-left:16px}
  .bullets li::before{content:"";position:absolute;left:2px;top:.62em;width:5px;height:5px;border-radius:50%;background:var(--muted)}

  .badges{position:absolute;right:30px;bottom:22px;display:flex;gap:16px;align-items:flex-end}
  .badge{width:40px;height:40px;border-radius:50%;border:3px solid var(--charcoal);background:var(--badge)}
  .badge--assoc{border-radius:4px;border:none;background:var(--badge)}

  /* front */
  .hero{position:absolute;left:0;top:0;width:520px;height:160px;
    background:linear-gradient(180deg,#ffffff 0%,#d9d9d9 45%,#8c8c8c 100%)}
  .card--front .brand{right:24px;top:22px}
  .headline{position:absolute;left:22px;top:108px;font-family:"Oswald",Impact,sans-serif;font-weight:700;
    font-size:50px;line-height:1;color:var(--orange);letter-spacing:1px;white-space:nowrap}
  .band{position:absolute;left:0;top:160px;width:520px;height:140px;background:var(--band)}
  .contact{position:absolute;list-style:none;color:var(--white);font-size:13px;line-height:22px}
  .contact li{display:flex;align-items:flex-start;gap:10px}
  .contact svg{flex:none;margin-top:4px}
  .contact--phones{left:26px;top:176px}
  .contact--web{left:218px;top:200px}
</style>
</head>
<body>
<main class="stage">

  <section class="card card--back" aria-label="Card back">
    <div class="brand"><span class="brand__dot"></span><span class="brand__name">Granite Rim Supply</span></div>
    <h2 class="services__title">SPECIALTY SERVICES</h2>
    <div class="services__rule"></div>

    <div class="range">
      <p class="range__title">SPECIALIZING IN NEW AND USED TIRES &amp; WHEELS FOR:</p>
      <ul class="range__list bullets">
        <li>Loaders</li>
        <li>Skid Steers</li>
        <li>Telehandlers</li>
        <li>Boom Lifts</li>
        <li>Forklifts and more</li>
      </ul>
    </div>

    <div class="downtime">
      <p class="downtime__title">ELIMINATING DOWNTIME</p>
      <p class="downtime__text">Wheel Exchange Program for New &amp; Used Foam Filled and Solid Rubber Tires</p>
    </div>

    <ul class="services__list bullets">
      <li>Rubber Tracks</li>
      <li>Foam Filling Tires</li>
      <li>Largest Tire Press in SE</li>
      <li>ONSITE Forklift Tire Press</li>
      <li>Boom Truck Services</li>
    </ul>
    <div class="badges">
      <span class="badge"></span>
      <span class="badge badge--assoc"></span>
    </div>
  </section>

  <section class="card card--front" aria-label="Card front">
    <div class="hero" role="img" aria-label="Close-up photo of stacked heavy equipment tires"></div>
    <div class="brand"><span class="brand__name">Granite Rim Supply</span><span class="brand__dot"></span></div>
    <div class="band"></div>
    <h1 class="headline">GRANITE RIM SUPPLY</h1>

    <ul class="contact contact--phones">
      <li><svg width="12" height="12" viewBox="0 0 12 12"><rect width="12" height="12" rx="2" fill="#fff"/><path d="M3.5 2.5l1.5 0 .6 2-1 .8a5 5 0 0 0 2.1 2.1l.8-1 2 .6v1.5c0 .5-.4.8-.9.8A6.5 6.5 0 0 1 2.7 3.4c0-.5.3-.9.8-.9z" fill="#4a4a4a"/></svg>844-GR-WHEEL</li>
      <li><svg width="12" height="12" viewBox="0 0 12 12"><rect width="12" height="12" rx="2" fill="#fff"/><rect x="4" y="2" width="4" height="8" rx="1" fill="#4a4a4a"/></svg>841-278-4120</li>
      <li><svg width="12" height="12" viewBox="0 0 12 12"><rect width="12" height="12" rx="2" fill="#fff"/><rect x="2.5" y="4" width="7" height="5" fill="#4a4a4a"/><rect x="4" y="2" width="4" height="2" fill="#4a4a4a"/></svg>561-278-9053</li>
    </ul>

    <ul class="contact contact--web">
      <li><svg width="12" height="12" viewBox="0 0 12 12"><rect width="12" height="12" rx="2" fill="#fff"/><circle cx="6" cy="6" r="3.5" fill="none" stroke="#4a4a4a" stroke-width="1.2"/><path d="M2.5 6h7" stroke="#4a4a4a" stroke-width="1"/></svg>www.graniterimsupply-example.com</li>
      <li><svg width="12" height="12" viewBox="0 0 12 12"><rect width="12" height="12" rx="2" fill="#fff"/><rect x="2" y="3.5" width="8" height="5" fill="none" stroke="#4a4a4a" stroke-width="1"/><path d="M2 3.5l4 3 4-3" fill="none" stroke="#4a4a4a" stroke-width="1"/></svg>info@graniterimsupply-example.com</li>
      <li><svg width="12" height="12" viewBox="0 0 12 12"><rect width="12" height="12" rx="2" fill="#fff"/><path d="M6 2a2.6 2.6 0 0 1 2.6 2.6C8.6 6.6 6 10 6 10S3.4 6.6 3.4 4.6A2.6 2.6 0 0 1 6 2z" fill="#4a4a4a"/></svg><span>5126 Marston Lane Harbor Pines<br>Florida 33480</span></li>
    </ul>
  </section>

</main>
</body>
</html>
```